Business Cards Needed for Innovative Healthcare Marketing Company

We are a marketing company focused on healthcare. Our company is all about rebranding yourself renewing your image and generating results. The phoenix stands for "reborn" or "rising" which we provide new brands for our clients we take their old brands and renew it with creativity and innovation. I am looking for a business card with color dimension. I have attached an example of a card I think has the look and feel of what I am trying to accomplish. I like that the card example has black and grey font colors, I like the font placement and the small logo, I really like the use of the colors on the right those are the colors of my logo. My logo is phoenix so maybe incorporating flames similar to that design. I would like the back a solid color maybe red with an opaque version of the logo and website. As a marketing company I am always open to creative liberty!

Target Market(s)

Doctors and business professionals.

Industry/Entity Type

Marketing

Contact Information for Business Card

Valcorne Health Care Marketing
Marla Tenwick- CEO
#(512)638-2974
email-marla@valcorne.com
website- valcorne.com

Font styles to use
Sans Serif

Colors
ec1f27
f37122
ffc214
fbed22
fbf289
f04a50

Requirements
Must have
• The logo and required information
Nice to have
• icons by the information
Should not have
• child like font

```html
<!DOCTYPE html>
<html lang="en">
<head>
<meta charset="utf-8">
<title>Valcorne Health Care Marketing – Business Card</title>
<link rel="stylesheet" href="https://fonts.googleapis.com/css2?family=Open+Sans:wght@300;400;700&display=swap">
<style>
  :root {
    --backdrop: #9b9b9b;
    --card-white: #f4f4f6;
    --brand-red: #8b1c1f;
    --brand-red-deep: #861a1e;
    --brand-rust: #a3361d;
    --brand-orange: #e8891e;
    --brand-gold: #d9a441;
    --text-grey: #3f3f44;
    --rule-grey: #8e8e92;
    --white: #ffffff;
  }
  * { box-sizing: border-box; margin: 0; padding: 0; }
  html, body {
    width: 1105px; height: 1200px; overflow: hidden;
    background: var(--backdrop);
    font-family: "Open Sans", Arial, sans-serif;
  }
  .canvas { position: relative; width: 1105px; height: 1200px; }

  .card {
    position: absolute; left: 180px; width: 745px; height: 428px;
    overflow: hidden;
  }
  .card--front { top: 120px; background: var(--card-white); }
  .card--back {
    top: 652px;
    background: linear-gradient(180deg, var(--brand-red-deep) 0%, var(--brand-red) 50%, var(--brand-rust) 100%);
  }

  /* brand lockup */
  .brand { position: absolute; display: flex; align-items: center; gap: 22px; }
  .brand__mark { width: 118px; height: 118px; border-radius: 50%; flex: none; }
  .brand__name {
    font-weight: 300; line-height: 1;
  }
  .brand__word { display: block; font-size: 50px; letter-spacing: 1px; }
  .brand__line {
    display: block; font-size: 15.5px; letter-spacing: 0.6px;
    margin-top: 9px; padding-top: 6px;
  }

  .card--front .brand { left: 318px; top: 40px; }
  .card--front .brand__mark { background: var(--brand-orange); }
  .card--front .brand__name { color: var(--brand-red); }
  .card--front .brand__line { border-top: 1px solid var(--rule-grey); }

  .card--back .brand { left: 160px; top: 128px; }
  .card--back .brand__mark { background: var(--white); width: 150px; height: 150px; }
  .card--back .brand__name { color: var(--white); }
  .card--back .brand__word { font-size: 56px; }
  .card--back .brand__line { font-size: 17px; border-top: 1px solid rgba(255,255,255,0.7); }

  /* contact block */
  .holder { position: absolute; left: 55px; top: 242px; right: 63px; }
  .holder__name {
    font-size: 23px; font-weight: 700; color: var(--brand-red);
    letter-spacing: 0.3px;
  }
  .holder__role-row { display: flex; align-items: center; gap: 8px; margin-top: 2px; }
  .holder__role { font-size: 17px; color: var(--brand-orange); font-weight: 400; }
  .holder__rule { flex: 1; height: 1px; background: var(--rule-grey); }

  .contact { position: absolute; left: 55px; top: 316px; list-style: none; }
  .contact__item {
    display: flex; align-items: center; gap: 12px;
    font-size: 18px; color: var(--text-grey); height: 28px;
  }
  .contact__icon { width: 17px; height: 17px; fill: var(--brand-red); }

  .website {
    position: absolute; right: 63px; top: 336px;
    font-size: 18px; color: var(--text-grey);
  }

  .edge-band { position: absolute; left: 0; right: 0; bottom: 0; height: 19px; background: var(--brand-red); }
  .edge-line { position: absolute; left: 0; right: 0; bottom: 19px; height: 3px; background: var(--brand-gold); }
</style>
</head>
<body>
<main class="canvas">

  <section class="card card--front" aria-label="Business card front">
    <div class="brand">
      <span class="brand__mark" aria-hidden="true"></span>
      <span class="brand__name">
        <span class="brand__word">VALCORNE</span>
        <span class="brand__line">HEALTH CARE MARKETING</span>
      </span>
    </div>

    <div class="holder">
      <h1 class="holder__name">MARLA TENWICK</h1>
      <div class="holder__role-row">
        <span class="holder__role">CEO</span>
        <span class="holder__rule"></span>
      </div>
    </div>

    <ul class="contact">
      <li class="contact__item">
        <svg class="contact__icon" viewBox="0 0 24 24" aria-hidden="true"><path d="M6.6 10.8c1.4 2.8 3.8 5.1 6.6 6.6l2.2-2.2c.3-.3.7-.4 1-.2 1.1.4 2.3.6 3.6.6.6 0 1 .4 1 1V20c0 .6-.4 1-1 1C10.6 21 3 13.4 3 4c0-.6.4-1 1-1h3.5c.6 0 1 .4 1 1 0 1.3.2 2.5.6 3.6.1.3 0 .7-.2 1z"/></svg>
        <span>(512)638-2974</span>
      </li>
      <li class="contact__item">
        <svg class="contact__icon" viewBox="0 0 24 24" aria-hidden="true"><path d="M2 5h20v14H2z M2 5l10 7 10-7" fill="var(--brand-red)"/><path d="M3 6l9 6.3L21 6" fill="none" stroke="var(--card-white)" stroke-width="1.6"/></svg>
        <span>marla@valcorne.com</span>
      </li>
    </ul>

    <p class="website">www.valcorne.com</p>

    <div class="edge-line"></div>
    <div class="edge-band"></div>
  </section>

  <section class="card card--back" aria-label="Business card back">
    <div class="brand">
      <span class="brand__mark" aria-hidden="true"></span>
      <span class="brand__name">
        <span class="brand__word">VALCORNE</span>
        <span class="brand__line">HEALTH CARE MARKETING</span>
      </span>
    </div>
  </section>

</main>
</body>
</html>
```